Drone service provider needs a brilliant web design

I need a responsive web design for a new drone service company. Pelham Drone Solutions provides turnkey solutions to capture, process, and deliver actionable aerial data to customers. The design should communicate a professional company that is safe, legal and insured. I included our logo design and business card designs for reference.
*content to be supplied after design selected

Target Market(s)

We serve telecommunications, construction, government, utility infrastructure, insurance and other industries.

Industry/Entity Type

Industrial

Number of Pages Required

5+ page

Colors

Designer to choose colors to be used in the design.

Requirements
Must have
• The design should highlight professional services to include Inspections, Mapping, Consulting and Training. The site should include aerial images and video to compliment the services offered. The landing page must include following sections in order: HOME, SERVICES, ABOUT, DEMO REEL, CLIENTS, CONTACT FORM, and social media buttons (Facebook, LinkedIn, Twitter, YouTube, Instagram). Contact: 615-382-9041 info@pelhamdronesolutions-example.com Smyrna, TN
• Sitemap:
• 6 pages: Home, Inspections, Mapping, Training, Consulting, About
• HOME (Landing Page)
• • Header with logo and tab links (Home, Services, About, Contact)
• • 'CAPTURE. PROCESS. DELIVER.' tagline and 'CONTACT US' button displayed within aerial image of drone over city or construction site
• • Services section with icons, text and read more link to page
• • About section with photo and text with three icons for SAFE. LEGAL. INSURED.
• • Demo reel
• • Clients logos shown scrolling horizontally
• • Contact form
• • Footer with logo, phone, email, social media buttons
• SERVICES (4 different pages)
• • Inspections
• • Mapping
• • Consulting
• • Training
• ABOUT page
• • Company
• • Partners
• • Certifications & Associations
• • Careers
• CONTACT linked to bottom of landing page
• Would you like to receive the newsletter? Yes or No Drop-down list
Nice to have
• Photos of KVR Marlin or Corvex inspecting infrastructure, buildings, construction sites, etc. A photo of one or two pilots in vest and helmet. Free stock photos preferred but would purchase the right photo that's more relevant.
• website references:
• https://www.quillrotor-example.com/
• https://www.brentfieldworks-example.com/services
• https://www.tomaro-example.com/
• http://gantrymetric-example.com/
• http://lumbrook-example.com/
• http://fennotics-example.com/
• https://www.grebe-example.io/
Should not have
• not an aerial photography or videography service business, no blog or newsletter

```html
<!DOCTYPE html>
<html lang="en">
<head>
<meta charset="utf-8">
<title>Pelham Drone Solutions</title>
<link rel="stylesheet" href="https://fonts.googleapis.com/css2?family=Montserrat:wght@400;600;700;800&family=Open+Sans:wght@400;600;700&display=swap">
<style>
:root{
  --blue:#1f8fd6;
  --blue-deep:#0b6fb8;
  --navy:#0b1f4d;
  --navy-dark:#050d26;
  --charcoal:#2b2b2b;
  --ink:#222;
  --muted:#666;
  --line:#dcdcdc;
  --white:#fff;
}
*{box-sizing:border-box;margin:0;padding:0}
html,body{width:1200px;height:3689px;overflow:hidden;background:var(--white)}
body{position:relative;font-family:"Open Sans",Arial,sans-serif;color:var(--ink)}
.abs{position:absolute}

/* header */
.site-header{left:0;top:0;width:1200px;height:110px;background:var(--blue)}
.nav-link{top:52px;font:600 15px/1 "Montserrat",Arial,sans-serif;color:var(--white);letter-spacing:.3px}
.brand{left:0;width:1200px;text-align:center;font:800 44px/1 "Montserrat",Arial,sans-serif;color:var(--charcoal);letter-spacing:1px}
.brand-sub{left:0;width:1200px;text-align:center;font:700 14px/1 "Montserrat",Arial,sans-serif;color:var(--blue);letter-spacing:3px}

/* hero */
.hero{left:0;top:110px;width:1200px;height:570px;background:linear-gradient(180deg,var(--navy-dark) 0%,var(--navy) 55%,#1c4a8c 100%)}
.hero-title{left:160px;top:232px;font:800 52px/62px "Montserrat",Arial,sans-serif;color:var(--white)}
.btn-light{display:flex;align-items:center;justify-content:center;background:var(--white);color:var(--blue);border-radius:5px;font:600 17px/1 "Open Sans",Arial,sans-serif}
.hero-arrows{left:160px;top:475px}

/* services */
.section-title{left:0;width:1200px;text-align:center;font:700 28px/1 "Montserrat",Arial,sans-serif;color:var(--blue)}
.title-rule{left:560px;width:80px;height:3px;background:var(--blue)}
.service-card{top:873px;width:236px;height:386px;background:var(--white);border:1px solid #e4e4e4;box-shadow:0 3px 10px rgba(0,0,0,.15)}
.service-photo{position:absolute;left:0;top:0;width:234px;height:172px}
.service-icon{position:absolute;left:87px;top:147px;width:60px;height:60px;border-radius:50%;background:var(--blue);border:4px solid var(--white);display:flex;align-items:center;justify-content:center}
.service-name{position:absolute;left:0;top:228px;width:234px;text-align:center;font:600 20px/1 "Open Sans",Arial,sans-serif;color:var(--ink)}
.service-text{position:absolute;left:18px;top:262px;width:198px;text-align:center;font:400 13px/21px "Open Sans",Arial,sans-serif;color:var(--muted)}
.read-more{position:absolute;left:0;top:346px;width:234px;text-align:center;font:700 12px/1 "Open Sans",Arial,sans-serif;color:var(--blue)}

/* about */
.about-bg{left:0;top:1330px}
.about-photo{left:98px;top:1483px;width:453px;height:337px;border:2px solid #ddd}
.about-video{left:248px;top:1721px;width:354px;height:185px;border:2px solid #ddd}
.about-kicker{left:610px;top:1478px;font:400 23px/1 "Open Sans",Arial,sans-serif;color:var(--white)}
.about-title{left:610px;top:1520px;font:600 34px/1 "Open Sans",Arial,sans-serif;color:var(--white)}
.pillar{top:1606px;width:170px;color:var(--white)}
.pillar-name{margin-top:14px;font:700 20px/1 "Montserrat",Arial,sans-serif}
.pillar-text{margin-top:10px;font:400 13px/19px "Open Sans",Arial,sans-serif;color:#ddd}
.about-body{left:610px;top:1798px;width:492px;font:400 11px/18px "Open Sans",Arial,sans-serif;color:#ddd}
.btn-blue{display:flex;align-items:center;justify-content:center;background:var(--blue);color:var(--white);font:700 12px/1 "Open Sans",Arial,sans-serif}

/* demo reel */
.reel{top:2107px;width:482px;height:271px;border:2px solid #333;overflow:hidden}
.play{position:absolute;left:50%;top:50%;transform:translate(-50%,-50%)}
.divider{left:98px;top:2476px;width:1004px;height:1px;background:var(--line)}
.client{top:2538px;width:133px;height:88px;border:1px solid var(--line);display:flex;align-items:center;justify-content:center;gap:6px;font:700 15px/1 "Open Sans",Arial,sans-serif;color:var(--ink)}
.client-dot{width:12px;height:12px;border-radius:50%;background:var(--ink)}

/* contact */
.contact{left:0;top:2685px;width:1200px;height:720px;background:linear-gradient(135deg,#2a9be0 0%,var(--blue) 50%,#1883c9 100%)}
.contact-title{left:0;top:2758px;width:1200px;text-align:center;font:700 28px/1 "Montserrat",Arial,sans-serif;color:var(--white)}
.contact-rule{left:560px;top:2806px;width:80px;height:2px;background:var(--white)}
.field{border:2px solid rgba(255,255,255,.85);border-radius:6px;padding:14px 12px;font:600 14px/1 "Open Sans",Arial,sans-serif;color:var(--white)}
.btn-submit{left:529px;top:3162px;width:142px;height:47px;font-size:14px}

/* footer */
.footer-bg{left:0;top:3290px}
.footer-brand{top:3370px;font-size:40px;color:var(--white)}
.footer-brand-sub{top:3414px;font-size:13px;color:var(--white)}
.footer-contacts{left:0;top:3476px;width:1200px;display:flex;justify-content:center;align-items:center;gap:36px}
.contact-line{display:flex;align-items:center;gap:10px;font:400 17px/1 "Open Sans",Arial,sans-serif;color:var(--white);white-space:nowrap}
.ring{flex:none;width:30px;height:30px;border:2px solid var(--white);border-radius:50%;display:flex;align-items:center;justify-content:center}
.footer-nav{left:0;top:3553px;width:1200px;text-align:center;font:600 14px/1 "Montserrat",Arial,sans-serif;color:var(--white);word-spacing:2px}
.footer-nav span.sep{margin:0 16px}
.footer-rule{left:98px;top:3610px;width:1004px;height:1px;background:#666}
.copyright{left:98px;top:3641px;font:400 13px/1 "Open Sans",Arial,sans-serif;color:var(--white)}
.socials{left:914px;top:3632px;display:flex;gap:12px}
.social{width:30px;height:30px;border:2px solid var(--white);border-radius:50%}
</style>
</head>
<body>

<!-- header -->
<header class="abs site-header"></header>
<svg class="abs" style="left:0;top:0" width="1200" height="170" viewBox="0 0 1200 170">
  <path d="M400 0 H800 L768 88 Q700 160 600 160 Q500 160 432 88 Z" fill="#fff"/>
</svg>
<a class="abs nav-link" style="left:98px">HOME</a>
<a class="abs nav-link" style="left:190px">ABOUT US</a>
<a class="abs nav-link" style="left:310px">SERVICES</a>
<a class="abs nav-link" style="left:821px">BLOG</a>
<a class="abs nav-link" style="left:905px">PRICING</a>
<a class="abs nav-link" style="left:1006px">CONTACT US</a>
<div class="abs brand" style="top:30px">PELHAM</div>
<div class="abs brand-sub" style="top:76px">DRONE SOLUTIONS</div>

<!-- hero -->
<section class="abs hero" role="img" aria-label="Drone flying above a city skyline at night"></section>
<svg class="abs" style="left:0;top:560px" width="1200" height="140" viewBox="0 0 1200 140">
  <path d="M0 40 Q600 120 1200 40 V140 H0 Z" fill="#fff"/>
  <path d="M0 40 Q600 120 1200 40" fill="none" stroke="#1f8fd6" stroke-width="8"/>
  <path d="M0 56 Q600 130 1200 56" fill="none" stroke="#1f8fd6" stroke-width="3" opacity=".6"/>
</svg>
<h1 class="abs hero-title">CAPTURE. PROCESS.<br>DELIVER.</h1>
<a class="abs btn-light" style="left:160px;top:384px;width:142px;height:49px">Contact Us</a>
<svg class="abs hero-arrows" width="60" height="24" viewBox="0 0 60 24">
  <path d="M14 3 L4 12 L14 21 M4 12 H24" fill="none" stroke="#fff" stroke-width="4"/>
  <path d="M46 3 L56 12 L46 21 M56 12 H36" fill="none" stroke="#fff" stroke-width="4"/>
</svg>

<!-- services -->
<h2 class="abs section-title" style="top:765px">OUR SERVICES</h2>
<div class="abs title-rule" style="top:814px"></div>

<article class="abs service-card" style="left:98px">
  <div class="service-photo" role="img" aria-label="Pilot holding a drone controller" style="background:linear-gradient(180deg,#b9c7d6,#55606b)"></div>
  <div class="service-icon"><svg width="26" height="26" viewBox="0 0 26 26"><circle cx="11" cy="11" r="7" fill="none" stroke="#fff" stroke-width="3"/><path d="M16 16 L23 23" stroke="#fff" stroke-width="3"/></svg></div>
  <h3 class="service-name">Inspections</h3>
  <p class="service-text">Lorem ipsum dolor sit amet, cons ectetur adipiscing elit, sed do eiusmod tempor</p>
  <a class="read-more">READ MORE</a>
</article>
<article class="abs service-card" style="left:354px">
  <div class="service-photo" role="img" aria-label="Aerial map view of a river through a town" style="background:linear-gradient(135deg,#2d5a5a,#6f8f86)"></div>
  <div class="service-icon"><svg width="24" height="26" viewBox="0 0 24 26"><path d="M12 1 C6 1 3 5 3 10 C3 16 12 25 12 25 C12 25 21 16 21 10 C21 5 18 1 12 1 Z" fill="#fff"/><circle cx="12" cy="10" r="3.5" fill="#1f8fd6"/></svg></div>
  <h3 class="service-name">Mapping</h3>
  <p class="service-text">Lorem ipsum dolor sit amet, cons ectetur adipiscing elit, sed do eiusmod tempor</p>
  <a class="read-more">READ MORE</a>
</article>
<article class="abs service-card" style="left:610px">
  <div class="service-photo" role="img" aria-label="Consultants meeting around a table" style="background:linear-gradient(135deg,#3b3631,#8a7563)"></div>
  <div class="service-icon"><svg width="28" height="24" viewBox="0 0 28 24"><ellipse cx="11" cy="9" rx="9" ry="7" fill="none" stroke="#fff" stroke-width="2.5"/><path d="M5 14 L3 20 L10 16" fill="#fff"/><path d="M20 10 Q26 11 26 16 Q26 19 23 20 L25 23 L19 21" fill="none" stroke="#fff" stroke-width="2"/></svg></div>
  <h3 class="service-name">Consulting</h3>
  <p class="service-text">Lorem ipsum dolor sit amet, cons ectetur adipiscing elit, sed do eiusmod tempor</p>
  <a class="read-more">READ MORE</a>
</article>
<article class="abs service-card" style="left:866px">
  <div class="service-photo" role="img" aria-label="Trainees on a field watching a drone flight" style="background:linear-gradient(180deg,#cfd6dc 0%,#9aa7a0 55%,#5f7a45 100%)"></div>
  <div class="service-icon"><svg width="26" height="26" viewBox="0 0 26 26"><circle cx="9" cy="9" r="5" fill="none" stroke="#fff" stroke-width="3" stroke-dasharray="3 2"/><circle cx="18" cy="18" r="5" fill="none" stroke="#fff" stroke-width="3" stroke-dasharray="3 2"/></svg></div>
  <h3 class="service-name">Training</h3>
  <p class="service-text">Lorem ipsum dolor sit amet, cons ectetur adipiscing elit, sed do eiusmod tempor</p>
  <a class="read-more">READ MORE</a>
</article>

<!-- about -->
<svg class="abs about-bg" width="1200" height="700" viewBox="0 0 1200 700">
  <path d="M0 50 Q600 -20 1200 50 V640 Q600 710 0 640 Z" fill="#2b2b2b"/>
</svg>
<div class="abs about-photo" role="img" aria-label="Drone flying over a city at sunrise" style="background:linear-gradient(135deg,#f2e6c8 0%,#c9a36a 50%,#6b6a6a 100%)"></div>
<div class="abs about-video" role="img" aria-label="Video still of green aerial landscape" style="background:linear-gradient(135deg,#1f3a1f,#4d6b3a)">
  <svg class="play" width="56" height="56" viewBox="0 0 56 56"><circle cx="28" cy="28" r="24" fill="none" stroke="#fff" stroke-width="4"/><path d="M22 17 L39 28 L22 39 Z" fill="#fff"/></svg>
</div>
<div class="abs about-kicker">About Us</div>
<h2 class="abs about-title">Pelham Drone Solutions</h2>

<div class="abs pillar" style="left:610px">
  <svg width="52" height="56" viewBox="0 0 52 56"><path d="M26 2 L44 9 V24 Q44 38 26 46 Q8 38 8 24 V9 Z" fill="none" stroke="#fff" stroke-width="3"/><path d="M18 24 L24 30 L35 18" fill="none" stroke="#fff" stroke-width="3"/><path d="M2 54 L14 44 Q20 40 26 44 L36 44" fill="none" stroke="#fff" stroke-width="3"/></svg>
  <div class="pillar-name">SAFE</div>
  <p class="pillar-text">Duis aute irure dolor in reprehenderit.</p>
</div>
<div class="abs pillar" style="left:792px">
  <svg width="52" height="56" viewBox="0 0 52 56"><rect x="8" y="3" width="34" height="48" fill="none" stroke="#fff" stroke-width="3"/><path d="M15 36 H35 M15 43 H35" stroke="#fff" stroke-width="3"/><text x="25" y="27" text-anchor="middle" font-family="Montserrat,Arial,sans-serif" font-size="20" font-weight="700" fill="#fff">$</text></svg>
  <div class="pillar-name">LEGAL</div>
  <p class="pillar-text">Duis aute irure dolor in reprehenderit.</p>
</div>
<div class="abs pillar" style="left:968px">
  <svg width="60" height="56" viewBox="0 0 60 56"><path d="M4 24 Q30 -8 56 24 Z" fill="#fff"/><path d="M30 24 V32" stroke="#fff" stroke-width="3"/><ellipse cx="22" cy="40" rx="10" ry="4" fill="#fff"/><ellipse cx="22" cy="47" rx="10" ry="4" fill="#fff"/><ellipse cx="40" cy="44" rx="10" ry="4" fill="#fff"/><ellipse cx="40" cy="51" rx="10" ry="4" fill="#fff"/></svg>
  <div class="pillar-name">INSURED</div>
  <p class="pillar-text">Duis aute irure dolor in reprehenderit.</p>
</div>
<p class="abs about-body">Nemo enim ipsam voluptatem quia voluptas sit aspernatur aut odit aut fugit, sed quia consequuntur magni dolores eos qui ratione voluptatem sequi nesciunt.</p>
<a class="abs btn-blue" style="left:610px;top:1871px;width:135px;height:40px">READ MORE &gt;</a>

<!-- demo reel -->
<div class="abs reel" style="left:98px;background:linear-gradient(160deg,#dfe9ee 0%,#4fb6c4 40%,#1d6f86 100%)" role="img" aria-label="Demo reel: aerial view of a coastline from a plane wing">
  <svg class="play" width="64" height="64" viewBox="0 0 64 64"><circle cx="32" cy="32" r="28" fill="none" stroke="#fff" stroke-width="4"/><path d="M25 19 L45 32 L25 45 Z" fill="#fff"/></svg>
</div>
<div class="abs reel" style="left:620px;background:linear-gradient(180deg,#b8c6cf 0%,#5f7a5a 45%,#486246 100%)" role="img" aria-label="Demo reel: aerial view of a residential neighbourhood">
  <svg class="play" width="64" height="64" viewBox="0 0 64 64"><circle cx="32" cy="32" r="28" fill="none" stroke="#fff" stroke-width="4"/><path d="M25 19 L45 32 L25 45 Z" fill="#fff"/></svg>
</div>

<div class="abs divider"></div>

<!-- clients -->
<div class="abs client" style="left:98px"><span class="client-dot"></span>Northfield</div>
<div class="abs client" style="left:275px">Corlane</div>
<div class="abs client" style="left:450px"><span class="client-dot"></span>Vantix</div>
<div class="abs client" style="left:622px"><span class="client-dot"></span>Northfield</div>
<div class="abs client" style="left:794px">Corlane</div>
<div class="abs client" style="left:969px"><span class="client-dot"></span>Vantix</div>

<!-- contact form -->
<section class="abs contact"></section>
<h2 class="abs contact-title">CONTACT FORM</h2>
<div class="abs contact-rule"></div>
<div class="abs field" style="left:125px;top:2887px;width:463px;height:50px">Name</div>
<div class="abs field" style="left:615px;top:2887px;width:460px;height:50px">Phone Number</div>
<div class="abs field" style="left:125px;top:2956px;width:950px;height:50px">Email Address</div>
<div class="abs field" style="left:125px;top:3025px;width:950px;height:98px">Message</div>
<a class="abs btn-light btn-submit">Submit Now</a>

<!-- footer -->
<svg class="abs footer-bg" width="1200" height="399" viewBox="0 0 1200 399">
  <path d="M0 80 Q600 -20 1200 80 V399 H0 Z" fill="#2b2b2b"/>
  <path d="M0 66 Q600 -34 1200 66" fill="none" stroke="#0d3f7a" stroke-width="6"/>
</svg>
<div class="abs brand footer-brand">PELHAM</div>
<div class="abs brand-sub footer-brand-sub">DRONE SOLUTIONS</div>
<div class="abs footer-contacts">
  <div class="contact-line">
    <span class="ring"><svg width="16" height="12" viewBox="0 0 16 12"><rect x="1" y="1" width="14" height="10" fill="none" stroke="#fff" stroke-width="1.6"/><path d="M1 1 L8 7 L15 1" fill="none" stroke="#fff" stroke-width="1.6"/></svg></span>
    <span>hello@pelhamdronesolutions-example.com</span>
  </div>
  <div class="contact-line">
    <span class="ring"><svg width="14" height="14" viewBox="0 0 14 14"><path d="M3 1 L5.5 4 L4 6 Q6 9 8 10 L10 8.5 L13 11 L11 13 Q5 12 1 3 Z" fill="#fff"/></svg></span>
    <span>615-382-9041</span>
  </div>
</div>
<nav class="abs footer-nav">HOME<span class="sep">|</span>ABOUT US<span class="sep">|</span>SERVICES<span class="sep">|</span>PRICING<span class="sep">|</span>BLOG<span class="sep">|</span>CONTACT US</nav>
<div class="abs footer-rule"></div>
<p class="abs copyright">Copyright © 2017 Pelham Drone Solutions. All Right Reserved</p>
<div class="abs socials" aria-label="Social media links">
  <span class="social"></span><span class="social"></span><span class="social"></span><span class="social"></span><span class="social"></span>
</div>

</body>
</html>
```